Frostvale Harborline LLC

we need a business card design

Industry/Entity Type

hvac

Contact Information for Business Card

my logo

Requirements
Must have
• my logo and same colors

```html
<!DOCTYPE html>
<html lang="en">
<head>
<meta charset="utf-8">
<title>Frostvale Harborline LLC – Business Card</title>
<link rel="stylesheet" href="https://fonts.googleapis.com/css2?family=Montserrat:wght@400;500;700;800&display=swap">
<style>
  :root {
    --stage: #2b2b2d;
    --brand-blue: #1f5ca8;
    --brand-blue-dark: #174a8c;
    --brand-gold: #f6b23c;
    --paper: #ffffff;
    --ink: #2a2a2a;
  }
  * { box-sizing: border-box; margin: 0; padding: 0; }
  html, body { width: 1200px; height: 874px; overflow: hidden; }
  body {
    background: var(--stage);
    font-family: "Montserrat", sans-serif;
    position: relative;
  }
  .card {
    position: absolute;
    width: 630px;
    height: 360px;
    border-radius: 26px;
    border: 5px solid var(--brand-gold);
  }
  .card--front {
    left: 200px;
    top: 56px;
    background: var(--brand-blue);
    display: flex;
    align-items: center;
    justify-content: center;
  }
  .front-mark {
    display: flex;
    align-items: center;
    gap: 16px;
  }
  .front-mark__dot {
    width: 26px; height: 26px; border-radius: 50%;
    background: var(--brand-gold);
  }
  .front-mark__name {
    color: var(--paper);
    font-weight: 800;
    font-size: 36px;
    line-height: 1.1;
    letter-spacing: .5px;
    text-transform: uppercase;
    text-align: left;
  }
  .card--back {
    left: 370px;
    top: 458px;
    background: var(--paper);
    display: flex;
    align-items: center;
    padding: 0 40px 0 46px;
  }
  .back-mark {
    width: 250px;
    display: flex;
    align-items: center;
    gap: 12px;
  }
  .back-mark__dot {
    flex: none;
    width: 18px; height: 18px; border-radius: 50%;
    background: var(--brand-gold);
  }
  .back-mark__name {
    color: var(--brand-blue);
    font-weight: 800;
    font-size: 22px;
    line-height: 1.15;
    text-transform: uppercase;
  }
  .contact {
    margin-left: 24px;
    border-left: 2px solid var(--brand-gold);
    padding-left: 16px;
    color: var(--ink);
    font-size: 14.5px;
    line-height: 1.35;
  }
  .contact__name {
    color: var(--brand-gold);
    font-weight: 700;
    font-size: 24px;
    line-height: 1.1;
  }
  .contact__title { font-weight: 500; margin-bottom: 6px; }
  .contact__address { margin-bottom: 6px; }
  .contact__row { display: flex; align-items: center; gap: 10px; }
  .contact__row svg { width: 14px; height: 14px; flex: none; fill: var(--brand-gold); }
</style>
</head>
<body>
  <section class="card card--front">
    <div class="front-mark">
      <span class="front-mark__dot"></span>
      <span class="front-mark__name">Frostvale<br>Harborline LLC</span>
    </div>
  </section>

  <section class="card card--back">
    <div class="back-mark">
      <span class="back-mark__dot"></span>
      <span class="back-mark__name">Frostvale Harborline LLC</span>
    </div>
    <div class="contact">
      <div class="contact__name">Dana Whitlock</div>
      <div class="contact__title">Managing Director</div>
      <div class="contact__address">48 Pier Lane,<br>Marlow, NY 13401</div>
      <div class="contact__row">
        <svg viewBox="0 0 14 14"><path d="M4 0h6a1.5 1.5 0 0 1 1.5 1.5v11A1.5 1.5 0 0 1 10 14H4a1.5 1.5 0 0 1-1.5-1.5v-11A1.5 1.5 0 0 1 4 0zm0 2v9h6V2zm3 9.6a.9.9 0 1 0 0 1.8.9.9 0 0 0 0-1.8z"/></svg>
        <span>+1 (555) 014-2290</span>
      </div>
      <div class="contact__row">
        <svg viewBox="0 0 14 14"><path d="M0 3h14v8H0zm1.2 1.2v.4L7 8l5.8-3.4v-.4z"/></svg>
        <span>hello@frostvaleharbor.com</span>
      </div>
      <div class="contact__row">
        <svg viewBox="0 0 14 14"><path d="M7 0a7 7 0 1 0 0 14A7 7 0 0 0 7 0zm0 1.4c.8 0 1.7 1.6 2 4.2H5c.3-2.6 1.2-4.2 2-4.2zM5 8.4h4c-.3 2.6-1.2 4.2-2 4.2s-1.7-1.6-2-4.2zM1.5 5.6h2.2c0-1.2.2-2.4.6-3.3A5.6 5.6 0 0 0 1.5 5.6zm0 2.8a5.6 5.6 0 0 0 2.8 3.3c-.4-.9-.6-2.1-.6-3.3zm11 0h-2.2c0 1.2-.2 2.4-.6 3.3a5.6 5.6 0 0 0 2.8-3.3zm0-2.8a5.6 5.6 0 0 0-2.8-3.3c.4.9.6 2.1.6 3.3z"/></svg>
        <span>www.frostvaleharbor.com</span>
      </div>
    </div>
  </section>
</body>
</html>
```